Redesign Craft Brewing Recipe Website

Originally built with Bootstrap just to get the site going, I am seeking a complete redesign of the sites home page and recipe page. I am an experienced web developer with no graphic background, initially just looking for psd mocks.

I prefer styles that are clean and modern, and would prefer anything that is fun, engaging, and has an organic feel to it. I currently have a cartoon rabbit as a logo, but it needs some modification/tweaking, so any help in that area would be great as well.

Current site:
http://velvetfinch.cloudpagehost.net/

Current launch page/logo:
http://www.velvetfinch.com/

I like the overall layout of the elements currently, but the design sucks.

The launch page is at the following URL

Reason: Still looking for a more modern design. Designs received so far are too similar to the original.

My site is content based and does not contain images or products. Your design should not consist of large images.

Reason: The website has very little images, so the designs need to be more text and content based. The header needs to be very small and should not contain an ad rotater.

Target Market(s)

Home brewers, Craft brewers, Microbreweries, Brewpubs

Requirements
Must have
• Web 2.0 Look and Feel, Fun, Hip, Focus on content
Should not have
• A large photo as a header

```html
<!DOCTYPE html>
<html lang="en">
<head>
<meta charset="utf-8">
<title>VelvetFinch – Craft Beer Recipes</title>
<link href="https://fonts.googleapis.com/css2?family=Open+Sans:wght@400;600;700&display=swap" rel="stylesheet">
<style>
:root{
  --orange:#f7820f;
  --orange-dark:#d96a00;
  --link:#1d9ad6;
  --text:#222;
  --muted:#555;
  --page:#f2f2f2;
  --panel:#f7f7f7;
  --line:#dedede;
  --tag-grey:#5b5b5b;
  --purple:#b23fd9;
  --green:#5cb82a;
}
*{box-sizing:border-box;margin:0;padding:0}
html,body{width:1200px;height:1039px;overflow:hidden}
body{background:var(--page);font-family:"Open Sans",Arial,sans-serif;color:var(--text);position:relative}
a{color:var(--link);text-decoration:none}

.site-header{position:absolute;left:0;top:0;width:1200px;height:168px;
  background:linear-gradient(#e9e9e9,#dcdcdc);border-top:4px solid var(--orange)}
.header-edge{position:absolute;left:0;top:160px}
.brand{position:absolute;left:116px;top:16px;display:flex;align-items:center;gap:8px}
.brand-mark{width:30px;height:30px;border-radius:50%;background:#3a3a3a}
.brand-name{font-size:28px;font-weight:700;color:#3a3a3a;letter-spacing:-.3px}
.header-rule{position:absolute;left:116px;top:70px;width:240px;height:1px;background:#cfcfcf}
.site-title{position:absolute;left:116px;top:80px;font-size:48px;font-weight:400;color:var(--orange);letter-spacing:.5px;line-height:1}
.tagline{position:absolute;left:118px;top:131px;font-size:14.8px;font-weight:700;color:#222;white-space:nowrap;width:530px}
.share{position:absolute;left:659px;top:132px;display:flex;gap:5px;font-size:9.5px}
.share span{border:1px solid #c9d3e6;background:#eef1f7;color:#3b5a98;padding:1px 4px;border-radius:2px}
.share .count{background:#fff;color:#333;border-color:#ccc}
.main-nav{position:absolute;left:893px;top:10px;font-size:17px;color:#333;display:flex;align-items:center;gap:4px}
.login-tab{position:absolute;left:982px;top:0;width:94px;height:32px;background:var(--orange);
  border-radius:0 0 10px 10px;color:#fff;font-weight:700;font-size:16px;text-align:center;line-height:30px}
.mascot{position:absolute;left:892px;top:44px;width:112px;height:140px;border-radius:50% 50% 40% 40%;
  background:radial-gradient(circle at 50% 40%,#ffffff,#e2e2e2)}

.filters{position:absolute;left:98px;top:212px;width:222px;height:480px;background:#fff;border:1px solid #e2e2e2;
  border-radius:4px;padding:12px 10px}
.search{display:flex;height:31px;border:1px solid #d6d6d6}
.search-input{flex:1;font-size:14px;color:#555;padding:5px 8px;background:#f5f5f5}
.search-go{width:34px;background:#8dcdf0;display:flex;align-items:center;justify-content:center}
.filter-head{font-size:12.5px;font-weight:600;color:#555;margin:13px 0 6px 4px;letter-spacing:.2px}
.filter-list{list-style:none}
.filter-list li{display:flex;align-items:center;gap:8px;height:25.7px;font-size:12.5px;border-bottom:1px solid #e3e3e3;padding-left:4px;width:176px}
.styles-box{position:relative}
.styles-box .filter-list li{width:186px;white-space:nowrap}
.box{width:11px;height:11px;border:1px solid #999;background:#fafafa;flex:none}
.scroll{position:absolute;left:194px;top:0;width:12px;height:204px;background:#f1f1f1;border-left:1px solid #ddd}
.scroll i{position:absolute;left:1px;top:14px;width:10px;height:12px;border:1px solid #999;background:#e9e9e9}

.tabs{position:absolute;left:366px;top:210px;display:flex;gap:7px}
.tab{width:108px;height:34px;text-align:center;line-height:34px;font-size:15px;font-weight:600}
.tab-active{background:var(--panel);border:1px solid var(--line);border-bottom:none;color:var(--link);font-weight:400}
.tab-idle{background:#bdbdbd;color:#222}

.recipes{position:absolute;left:342px;top:243px;width:763px;height:696px;background:var(--panel);border:1px solid var(--line);
  display:grid;grid-template-columns:1fr 1fr;grid-template-rows:227px 230px 1fr;padding:14px 20px 0 22px;column-gap:32px}
.recipe{padding-top:4px;position:relative}
.recipe:nth-child(odd){border-right:1px solid var(--line);padding-right:14px}
.recipe:nth-child(n+3){border-top:1px solid var(--line)}
.recipe:nth-child(n+3){padding-top:7px}
.recipe h2{font-size:16px;font-weight:700;color:var(--link);margin-bottom:9px}
.recipe p{font-size:12.3px;line-height:17px;color:#333;width:330px}
.author{font-size:12.3px;color:#555;margin:17px 0 9px}
.tags{display:flex;gap:5px;margin-bottom:14px}
.tag{font-size:12.3px;font-weight:700;color:#fff;padding:4px 8px;border:1px solid rgba(0,0,0,.15)}
.tag-grey{background:var(--tag-grey)}
.stats{display:flex;width:344px;height:57px;border:1px solid #ddd}
.stat{flex:1;display:flex;flex-direction:column;justify-content:center;align-items:center;font-size:12.5px;line-height:19px;
  background:linear-gradient(#fafafa,#e6e6e6);border-right:1px solid #ddd}
.stat.srm{color:#fff;border:none}

.site-footer{position:absolute;left:0;top:968px;width:1200px;height:71px;background:#fff;border-top:1px solid #e5e5e5;
  padding:17px 0 0 104px;font-size:12.5px;color:#444}
.site-footer nav{margin-top:8px;display:flex;gap:8px;color:var(--link)}
</style>
</head>
<body>
<header class="site-header">
  <div class="brand"><span class="brand-mark"></span><span class="brand-name">VelvetFinch</span></div>
  <div class="header-rule"></div>
  <h1 class="site-title">VELVETFINCH</h1>
  <div class="tagline">Velvetfinch is the easiest way to create and share craft beer recipes.</div>
  <div class="share"><span>Like</span><span class="count">0</span><span>Send</span></div>
  <nav class="main-nav">
    <svg width="12" height="16" viewBox="0 0 12 16"><path d="M2 0v6M4 0v6M6 0v6M2 6h4M4 6v10M10 0c-2 2-2 6 0 7v9" stroke="#333" stroke-width="1.6" fill="none"/></svg>
    Recipes
  </nav>
  <div class="login-tab">Login</div>
  <div class="mascot" role="img" aria-label="White cartoon mascot character"></div>
</header>
<svg class="header-edge" width="1200" height="8" viewBox="0 0 1200 8">
  <defs><pattern id="zig" width="8" height="8" patternUnits="userSpaceOnUse"><path d="M0 0L4 6L8 0Z" fill="#dcdcdc"/></pattern></defs>
  <rect width="1200" height="8" fill="url(#zig)"/>
</svg>

<aside class="filters">
  <div class="search"><div class="search-input">Stout</div>
    <div class="search-go"><svg width="10" height="12" viewBox="0 0 10 12"><path d="M2 1l5 5-5 5" stroke="#1d7fc0" stroke-width="2.4" fill="none"/></svg></div></div>
  <div class="filter-head">BREWING</div>
  <ul class="filter-list">
    <li><span class="box"></span>Extract</li>
    <li><span class="box"></span>Partial Mash</li>
    <li><span class="box"></span>All Grain</li>
  </ul>
  <div class="filter-head" style="margin-top:20px">STYLES</div>
  <div class="styles-box">
    <ul class="filter-list">
      <li><span class="box"></span>American Amber Ale</li>
      <li><span class="box"></span>American Barleywine</li>
      <li><span class="box"></span>American Brown Ale</li>
      <li><span class="box"></span>American IPA</li>
      <li><span class="box"></span>American Pale Ale</li>
      <li><span class="box"></span>American Stout</li>
      <li><span class="box"></span>American Wheat or Rye Beer</li>
      <li><span class="box"></span>Applewine</li>
    </ul>
    <div class="scroll"><i></i></div>
  </div>
  <div class="filter-head" style="margin-top:20px">MATCH MAKER</div>
  <ul class="filter-list"><li><span class="box"></span>Boil Size</li></ul>
</aside>

<div class="tabs"><div class="tab tab-active">Recent</div><div class="tab tab-idle">Popular</div></div>

<main class="recipes">
  <article class="recipe">
    <h2>Venom Belgian Specialty Ale</h2>
    <p>Lorem ipsum dolor sit amet, consectetur adipisicing elit, sed do eiusmod tempor incididunt ut labore et dolore</p>
    <div class="author">created by <a href="#">Daniel Marsh</a></div>
    <div class="tags"><span class="tag" style="background:var(--purple)">PartialMash</span><span class="tag tag-grey">Belgian Specialty Ale</span></div>
    <div class="stats"><div class="stat">13.93%<span>abv</span></div><div class="stat">126<span>ibu</span></div><div class="stat">1.036<span>fg</span></div><div class="stat">1.139<span>og</span></div><div class="stat srm" style="background:#4f9e12">28<span>srm</span></div></div>
  </article>
  <article class="recipe">
    <h2>Hooker German Pilsner (Pils)</h2>
    <p>Lorem ipsum dolor sit amet, consectetur adipisicing elit, sed do eiusmod tempor incididunt ut labore et dolore</p>
    <div class="author">created by <a href="#">Daniel Marsh</a></div>
    <div class="tags"><span class="tag" style="background:var(--orange)">PartialMash</span><span class="tag tag-grey">Belgian Specialty Ale</span></div>
    <div class="stats"><div class="stat">13.93%<span>abv</span></div><div class="stat">126<span>ibu</span></div><div class="stat">1.036<span>fg</span></div><div class="stat">1.139<span>og</span></div><div class="stat srm" style="background:#ff8000">28<span>srm</span></div></div>
  </article>
  <article class="recipe">
    <h2>Honeysucker Belgian Tripel</h2>
    <p>Lorem ipsum dolor sit amet, consectetur adipisicing elit, sed do eiusmod tempor incididunt ut labore et dolore</p>
    <div class="author">created by <a href="#">Daniel Marsh</a></div>
    <div class="tags"><span class="tag" style="background:var(--orange)">PartialMash</span><span class="tag tag-grey">Belgian Specialty Ale</span></div>
    <div class="stats"><div class="stat">13.93%<span>abv</span></div><div class="stat">126<span>ibu</span></div><div class="stat">1.036<span>fg</span></div><div class="stat">1.139<span>og</span></div><div class="stat srm" style="background:#4a4a4a">28<span>srm</span></div></div>
  </article>
  <article class="recipe">
    <h2>Oak Bastard Sweet Mead</h2>
    <p>Lorem ipsum dolor sit amet, consectetur adipisicing elit, sed do eiusmod tempor incididunt ut labore et dolore</p>
    <div class="author">created by <a href="#">Daniel Marsh</a></div>
    <div class="tags"><span class="tag" style="background:var(--orange)">PartialMash</span><span class="tag tag-grey">Belgian Specialty Ale</span></div>
    <div class="stats"><div class="stat">13.93%<span>abv</span></div><div class="stat">126<span>ibu</span></div><div class="stat">1.036<span>fg</span></div><div class="stat">1.139<span>og</span></div><div class="stat srm" style="background:#6f119c">28<span>srm</span></div></div>
  </article>
  <article class="recipe">
    <h2>Oak Bastard Dry Mead</h2>
    <p>Lorem ipsum dolor sit amet, consectetur adipisicing elit, sed do eiusmod tempor incididunt ut labore et dolore</p>
    <div class="author">created by <a href="#">Daniel Marsh</a></div>
    <div class="tags"><span class="tag" style="background:var(--orange)">PartialMash</span><span class="tag tag-grey">Belgian Specialty Ale</span></div>
    <div class="stats"><div class="stat">13.93%<span>abv</span></div><div class="stat">126<span>ibu</span></div><div class="stat">1.036<span>fg</span></div><div class="stat">1.139<span>og</span></div><div class="stat srm" style="background:#c77800">28<span>srm</span></div></div>
  </article>
  <article class="recipe">
    <h2>Venom Mild</h2>
    <p>Lorem ipsum dolor sit amet, consectetur adipisicing elit, sed do eiusmod tempor incididunt ut labore et dolore</p>
    <div class="author">created by <a href="#">Daniel Marsh</a></div>
    <div class="tags"><span class="tag" style="background:var(--green)">PartialMash</span><span class="tag tag-grey">Belgian Specialty Ale</span></div>
    <div class="stats"><div class="stat">13.93%<span>abv</span></div><div class="stat">126<span>ibu</span></div><div class="stat">1.036<span>fg</span></div><div class="stat">1.139<span>og</span></div><div class="stat srm" style="background:#1a73e0">28<span>srm</span></div></div>
  </article>
</main>

<footer class="site-footer">
  © Velvetfinch, Inc. All third party content © their respective owners.
  <nav><a href="#">Terms of Service</a><span>|</span><a href="#">Contact</a></nav>
</footer>
</body>
</html>
```